Book for new dads needs a cover.

We need a cover for a book titled Roadmap to Early Parenthood: Practical Methods for Welcoming a Newborn, Juggling Career and Home Life, and Managing Mental Health on the Path to Becoming a Parent. We would like to see a design that emphasizes healthy babies and confident dads.

```html
<!DOCTYPE html>
<html lang="en">
<head>
<meta charset="utf-8">
<title>Roadmap to Early Parenthood — Book Cover</title>
<link rel="stylesheet" href="https://fonts.googleapis.com/css2?family=Oswald:wght@600&family=Great+Vibes&family=Arimo:ital,wght@0,400;0,700;1,400&display=swap">
<style>
  :root {
    --surround: #262626;
    --paper: #ffffff;
    --brand-blue: #087cc6;
    --gold: #cc9604;
    --ink: #1c1c1c;
    --photo-light: #f1f3f4;
    --photo-mid: #c9cdd1;
    --photo-warm: #b08a70;
  }
  * { margin: 0; padding: 0; box-sizing: border-box; }
  html, body {
    width: 1200px; height: 1200px; overflow: hidden;
    background: var(--surround);
  }
  .cover {
    position: absolute; left: 216px; top: 25px;
    width: 767px; height: 1150px;
    background: var(--paper);
    overflow: hidden;
  }
  .author {
    position: absolute; top: 76px; left: 62px; right: 58px;
    display: flex; align-items: center; gap: 26px;
    font-family: "Arimo", Arial, sans-serif;
    font-size: 27px; letter-spacing: 1.5px; color: #000;
  }
  .author::before, .author::after {
    content: ""; flex: 1; height: 2px; background: #000;
  }
  .title {
    position: absolute; left: 0; right: 0; top: 118px;
    text-align: center;
  }
  .title-main {
    display: block;
    font-family: "Oswald", "Arial Narrow", sans-serif;
    font-weight: 600; font-size: 186px; line-height: 186px;
    color: var(--brand-blue); text-transform: uppercase;
  }
  .title-mid {
    display: block; margin-top: -22px;
    font-family: "Oswald", "Arial Narrow", sans-serif;
    font-weight: 600; font-size: 124px; line-height: 124px;
    color: var(--gold); text-transform: uppercase;
  }
  .title-script {
    display: block; margin-top: -40px;
    font-family: "Great Vibes", cursive;
    font-size: 138px; line-height: 150px;
    color: var(--brand-blue);
  }
  .subtitle {
    position: absolute; top: 533px; left: 50px; right: 50px;
    text-align: center; font-family: "Arimo", Arial, sans-serif;
  }
  .subtitle-lead {
    display: block; font-weight: 700; font-size: 23px;
    color: var(--brand-blue); margin-bottom: 5px;
  }
  .subtitle-rest {
    display: block; font-style: italic; font-size: 19.5px;
    line-height: 27px; color: var(--ink);
  }
  .hero-photo {
    position: absolute; left: 80px; top: 615px;
    width: 610px; height: 535px;
    border-radius: 48% 48% 0 0 / 38% 38% 0 0;
    background:
      radial-gradient(ellipse at 62% 28%, var(--photo-warm) 0%, rgba(176,138,112,0) 42%),
      radial-gradient(ellipse at 30% 45%, #f0d9c8 0%, rgba(240,217,200,0) 40%),
      linear-gradient(180deg, var(--photo-light) 0%, var(--photo-mid) 100%);
  }
</style>
</head>
<body>
  <main class="cover">
    <p class="author">AUTHOR NAME</p>
    <h1 class="title">
      <span class="title-main">Roadmap</span>
      <span class="title-mid">To Early</span>
      <span class="title-script">Parenthood</span>
    </h1>
    <p class="subtitle">
      <span class="subtitle-lead">Practical Methods for Welcoming</span>
      <span class="subtitle-rest">a Newborn, Juggling Career and Home Life, and Managing Mental Health on the Path to Becoming a Parent.</span>
    </p>
    <div class="hero-photo" role="img" aria-label="Photo of a smiling father in a grey hoodie holding his happy baby close, cheek to cheek"></div>
  </main>
</body>
</html>
```